Bright Harbor Design

We need a web design for our startup company based in Zurich, Switzerland called Bright Harbor. We offer professional flirt and dating advice, self development with seminars and practical coachings.

The final website aims for two capital goals. First, it will contain text, pictures and video based content presenting and advertising our services. Furthermore, we want to bind our costumers with a plattform offering them to share their expiriences related with our services.

The targeted group will be men from 25 to 40 years.
Updates

The design requires also a register-box to put in the clients Name and Email

I need (besides of the "email registration box") a "Video Gallery", "Blog" and "Agenda (with the next events to come)"

Reason: I want to make a poll now

Target Market(s)

Guys around 25 to 40 years who want to improve their social lifestyle

Industry/Entity Type

Advertising

Requirements
Must have
• First and foremost, the design must transfer strong emotions and suggest an attractive social lifestyle.

The design should not be overloaded with content but should include pictures, videos and text.

The design should present a modern, urban lifestyle.
Nice to have
• There is a logo attached to the assignement. However, if you have a good idea for an improved or different logo, please do not hesitate to design your ideas.

```html
<!DOCTYPE html>
<html lang="en">
<head>
<meta charset="utf-8">
<title>Bright Harbor – Dating &amp; Flirting Advice</title>
<link rel="stylesheet" href="https://fonts.googleapis.com/css2?family=PT+Sans:ital,wght@0,400;0,700;1,400;1,700&display=swap">
<style>
:root{
  --navy:#1b2f55;
  --blue:#1a7fc4;
  --blue-dark:#0f5f9e;
  --blue-bar:#3ea3dc;
  --text:#3a3a3a;
  --muted:#555;
  --white:#fff;
  --orange-top:#ffb347;
  --orange-bot:#f46f12;
  --line:#d6dde3;
}
*{margin:0;padding:0;box-sizing:border-box}
html,body{width:1200px;height:1186px;overflow:hidden;background:#fff}
body{font-family:"PT Sans",sans-serif;color:var(--text)}
.page{position:absolute;left:0;top:0;width:1400px;height:1384px;transform:scale(.857143);transform-origin:0 0}
.abs{position:absolute}
.heading{position:absolute;font-style:italic;font-weight:700;font-size:25px;color:var(--blue);letter-spacing:-.8px}

/* header */
.brand{left:220px;top:70px;display:flex;align-items:center;gap:14px}
.brand-dot{width:60px;height:60px;border-radius:50%;background:var(--navy)}
.brand-name{font-size:36px;font-weight:700;color:var(--navy)}
.nav{left:549px;top:104px;width:633px;height:39px;border-radius:4px;background:linear-gradient(#5fbdec,#1f86cc);border:1px solid #1a73b3;display:flex;justify-content:space-around;align-items:center;list-style:none}
.nav li{color:var(--white);font-size:12px;text-transform:uppercase;letter-spacing:-.2px}

/* hero */
.hero{left:218px;top:168px;width:964px;height:371px;overflow:hidden;background:linear-gradient(90deg,#8fcaa9 0%,#a9d6c4 30%,#bfdcdc 55%,#a7cdd6 100%)}
.hero-fade{left:0;top:0;width:964px;height:80px;background:linear-gradient(#fff,rgba(255,255,255,0))}
.hero-scene{left:540px;top:0;width:424px;height:371px;background:linear-gradient(160deg,rgba(200,225,235,.5),rgba(190,175,120,.55))}
.frame{position:absolute;background:var(--white);box-shadow:0 2px 6px rgba(0,0,0,.3)}
.frame-back1{left:30px;top:30px;width:490px;height:318px;transform:rotate(3deg)}
.frame-back2{left:28px;top:40px;width:490px;height:300px;transform:rotate(-2deg)}
.frame-main{left:35px;top:43px;width:497px;height:292px}
.photo-main{left:10px;top:11px;width:477px;height:272px;background:linear-gradient(135deg,#6e6a66,#9a948c 50%,#4a4541)}
.hero-title1{left:812px;top:254px;font-style:italic;font-weight:700;font-size:34px;color:var(--navy);letter-spacing:-1.5px}
.hero-title2{left:812px;top:292px;font-style:italic;font-weight:700;font-size:39px;color:var(--blue);letter-spacing:-1.5px}
.hero-text{left:815px;top:343px;width:330px;font-size:12.5px;line-height:18px;color:#1d2a33}
.btn-cta{left:816px;top:392px;width:198px;height:43px;border-radius:4px;background:linear-gradient(var(--orange-top),var(--orange-bot));color:var(--white);font-style:italic;font-size:26px;text-align:center;line-height:43px;letter-spacing:-1px}
.dots{left:1104px;top:516px;display:flex;gap:3px}
.dots span{width:11px;height:11px;background:rgba(255,255,255,.6)}
.dots span:first-child{background:var(--white)}

/* videos */
.video{left:219px;top:603px;width:280px;height:227px;background:#1d1915;border:2px solid #111}
.video-frame{left:4px;top:4px;width:270px;height:196px;background:linear-gradient(135deg,#5b4b3a,#2e261f 50%,#6b5440)}
.controls{left:0;top:201px;width:276px;height:22px;background:linear-gradient(#3b3b3b,#111);color:#ddd;font-size:11px}

/* welcome */
.welcome-frame{left:538px;top:599px;width:360px;height:127px;background:#fff;border:1px solid var(--line);box-shadow:0 1px 3px rgba(0,0,0,.15)}
.welcome-photo{left:7px;top:7px;width:345px;height:112px;background:linear-gradient(#7fb7e6,#c9a483 70%,#3aa3a8)}
.welcome-text{left:538px;top:736px;width:372px;font-size:11px;line-height:18px;color:var(--muted)}

/* services */
.services-head{left:930px;top:574px;width:252px;height:33px;border-radius:4px 4px 0 0;background:linear-gradient(#5fbdec,#1f86cc);color:var(--white);font-size:17px;line-height:33px;padding-left:16px}
.services-list{left:930px;top:614px;width:252px;height:204px;border:1px solid var(--line);border-radius:4px;list-style:none;padding:12px 0 0 27px}
.services-list li{font-size:12px;height:26px;line-height:18px;color:#333;display:flex;align-items:center;gap:8px}
.services-list li::before{content:"";width:11px;height:11px;border-radius:50%;background:radial-gradient(circle at 40% 40%,#8fd0f5,#1f7fc4)}

/* arrows */
.circle-arrow{position:absolute;border-radius:50%;background:linear-gradient(#5fbdec,#1a73b8)}

/* blog */
.blog-band{left:216px;top:889px;width:966px;height:133px;border-radius:4px;background:linear-gradient(#e9ecee,#fff)}
.post{position:absolute;top:911px;width:290px;height:110px}
.post-frame{left:0;top:0;width:103px;height:88px;background:#fff;border:1px solid #ddd;box-shadow:0 1px 3px rgba(0,0,0,.2)}
.post-photo{left:6px;top:6px;width:89px;height:74px;background:linear-gradient(135deg,#c9a07e,#8fb8d4)}
.post-title{left:119px;top:0;font-size:13px;color:var(--blue)}
.post-text{left:119px;top:25px;width:150px;font-size:11px;line-height:18px;color:var(--muted)}
.btn-read{left:192px;top:86px;width:70px;height:20px;border-radius:3px;background:linear-gradient(#5fbdec,#1a78c0);color:#fff;font-size:11px;text-align:center;line-height:20px}
.sep{position:absolute;top:914px;height:94px;border-left:1px dotted #aaa}

/* gallery */
.gallery-band{left:217px;top:1074px;width:965px;height:146px;border-radius:4px 4px 0 0;background:linear-gradient(#2f97d6,#8ccbee 70%,#fff)}
.g-frame{position:absolute;top:1090px;width:169px;height:118px;background:#fff;box-shadow:0 2px 5px rgba(0,0,0,.25)}
.g-photo{position:absolute;left:7px;top:7px;width:155px;height:104px}
.g-arrow{position:absolute;top:1137px;width:14px;height:14px;border-radius:50%;background:#fff;border:1px solid #999}

/* footer */
.footer{left:216px;top:1241px;width:966px;height:96px;border-radius:4px;background:var(--blue-bar);color:var(--white)}
.footer-links{left:26px;top:30px;display:flex;font-size:11px;list-style:none}
.footer-links li+li::before{content:"|";margin:0 16px}
.copyright{left:26px;top:50px;font-size:11px}
.copyright span{color:#bfe6ff}
.connect{left:695px;top:32px;width:100px;text-align:right;font-size:11px;line-height:15px}
.social{position:absolute;top:1271px;width:32px;height:32px;border-radius:50%}
</style>
</head>
<body>
<div class="page">

  <header>
    <div class="abs brand"><span class="brand-dot"></span><span class="brand-name">Bright Harbor</span></div>
    <ul class="abs nav">
      <li>Home</li><li>About us</li><li>Our services</li><li>Video</li><li>Gallery</li><li>Contact us</li>
    </ul>
  </header>

  <section class="abs hero">
    <div class="abs hero-scene" role="img" aria-label="Couple embracing in a field of tall grass"></div>
    <div class="abs hero-fade"></div>
    <div class="frame frame-back1"></div>
    <div class="frame frame-back2"></div>
    <div class="frame frame-main">
      <div class="abs photo-main" role="img" aria-label="Man and woman chatting on a busy city street"></div>
    </div>
  </section>
  <h1 class="abs hero-title1">Bright Harbor is a</h1>
  <h2 class="abs hero-title2">Dating &amp; Flirting advise</h2>
  <p class="abs hero-text">Lorem Ipsum is simply dummy text of the printing and typesetting industry. Lorem Ipsum has been the industry's.</p>
  <div class="abs btn-cta">Get Connected</div>
  <div class="abs dots"><span></span><span></span><span></span><span></span><span></span></div>

  <h2 class="heading" style="left:220px;top:560px">Our Videos</h2>
  <div class="abs video">
    <div class="abs video-frame" role="img" aria-label="Video still of a man meeting a woman in a shop"></div>
    <svg class="abs" style="left:108px;top:80px" width="48" height="48" viewBox="0 0 48 48">
      <circle cx="24" cy="24" r="22" fill="#222" stroke="#777" stroke-width="2"/>
      <path d="M18 13 L35 24 L18 35 Z" fill="#fff"/>
    </svg>
    <div class="abs controls">
      <svg class="abs" style="left:8px;top:5px" width="12" height="12"><rect x="1" y="0" width="3" height="12" fill="#ccc"/><rect x="7" y="0" width="3" height="12" fill="#ccc"/></svg>
      <svg class="abs" style="left:34px;top:5px" width="20" height="12"><path d="M0 4h4l5-4v12l-5-4H0z" fill="#999"/><rect x="12" y="3" width="2" height="6" fill="#777"/><rect x="16" y="1" width="2" height="10" fill="#777"/></svg>
      <span class="abs" style="left:64px;top:4px">0:04 / 0:30</span>
      <svg class="abs" style="left:134px;top:5px" width="102" height="12"><rect x="0" y="3" width="100" height="6" fill="#000"/><rect x="0" y="3" width="52" height="6" fill="#555"/><rect x="0" y="3" width="8" height="6" fill="#d22"/><circle cx="14" cy="6" r="6" fill="#ddd"/></svg>
      <svg class="abs" style="left:254px;top:5px" width="12" height="12"><path d="M0 0h4M0 0v4M12 0H8M12 0v4M0 12h4M0 12V8M12 12H8M12 12V8" stroke="#888" stroke-width="2"/></svg>
    </div>
  </div>

  <h2 class="heading" style="left:537px;top:560px">Welcome to Bright Harbor</h2>
  <div class="abs welcome-frame">
    <div class="abs welcome-photo" role="img" aria-label="Smiling couple at the beach"></div>
  </div>
  <p class="abs welcome-text">Lorem Ipsum is simply dummy text of the printing and typesetting industry. Lorem Ipsum has been the industry's standard dummy text ever since the 1500s, when an unknown printer took a galley of type and scrambled it to make a type specimen book. It has survived not only five centuries, but also the leap into electronic typesetting, remaining essentially unchanged.</p>

  <div class="abs services-head">Our Services</div>
  <ul class="abs services-list">
    <li>Relationship Advice</li>
    <li>Relationship Issues</li>
    <li>Love Research Project</li>
    <li>Latest Articles</li>
    <li>Supporting yourself</li>
    <li>Finding Time for Each Other</li>
    <li>Getting on Better with my Partner</li>
  </ul>

  <h2 class="heading" style="left:218px;top:850px">Recent Blog</h2>
  <svg class="abs" style="left:1126px;top:855px" width="48" height="20" viewBox="0 0 48 20">
    <circle cx="10" cy="10" r="10" fill="#2a8ad0"/><path d="M12 6l-5 4 5 4z" fill="#fff"/>
    <circle cx="37" cy="10" r="10" fill="#2a8ad0"/><path d="M35 6l5 4-5 4z" fill="#fff"/>
  </svg>
  <div class="abs blog-band"></div>
  <article class="post" style="left:234px">
    <div class="abs post-frame"><div class="abs post-photo" role="img" aria-label="Happy couple portrait"></div></div>
    <h3 class="abs post-title">Lorem Ipsum is simply</h3>
    <p class="abs post-text">Lorem Ipsum is simply dummy text of the printing and type-setting industry.</p>
    <div class="abs btn-read">Readmore</div>
  </article>
  <div class="sep" style="left:531px"></div>
  <article class="post" style="left:561px">
    <div class="abs post-frame"><div class="abs post-photo" role="img" aria-label="Couple smiling together"></div></div>
    <h3 class="abs post-title">Lorem Ipsum is simply</h3>
    <p class="abs post-text">Lorem Ipsum is simply dummy text of the printing and type-setting industry.</p>
    <div class="abs btn-read">Readmore</div>
  </article>
  <div class="sep" style="left:859px"></div>
  <article class="post" style="left:894px">
    <div class="abs post-frame"><div class="abs post-photo" role="img" aria-label="Young couple hugging"></div></div>
    <h3 class="abs post-title">Lorem Ipsum is simply</h3>
    <p class="abs post-text">Lorem Ipsum is simply dummy text of the printing and type-setting industry.</p>
    <div class="abs btn-read">Readmore</div>
  </article>

  <h2 class="heading" style="left:222px;top:1036px">Photo galery</h2>
  <div class="abs gallery-band"></div>
  <div class="g-arrow" style="left:223px"></div>
  <div class="g-frame" style="left:242px"><div class="g-photo" role="img" aria-label="Couple relaxing on the beach" style="background:linear-gradient(135deg,#9cc6df,#e3c8a8)"></div></div>
  <div class="g-frame" style="left:429px"><div class="g-photo" role="img" aria-label="Couple laughing outdoors" style="background:linear-gradient(135deg,#f0f0f0,#d8a98a)"></div></div>
  <div class="g-frame" style="left:615px"><div class="g-photo" role="img" aria-label="Couple close together" style="background:linear-gradient(135deg,#7a4a32,#d7a582)"></div></div>
  <div class="g-frame" style="left:802px"><div class="g-photo" role="img" aria-label="Man with raised arms in a sunny field" style="background:linear-gradient(#f7e27a,#e0b820 60%,#8a9a20)"></div></div>
  <div class="g-frame" style="left:989px"><div class="g-photo" role="img" aria-label="Couple sitting on a park bench" style="background:linear-gradient(135deg,#6f9a3c,#c9b080)"></div></div>
  <div class="g-arrow" style="left:1165px"></div>

  <footer class="abs footer">
    <ul class="abs footer-links">
      <li>Home</li><li>About us</li><li>Our Services</li><li>Video</li><li>Gallery</li><li>Contact us</li>
    </ul>
    <p class="abs copyright">Copyright © 2013 <span>Bright Harbor</span>. All Rights Reserved.</p>
    <p class="abs connect">Connect to<br>our Social Network :</p>
  </footer>
  <span class="social" style="left:1018px;background:#2f5fa8" aria-label="Social network"></span>
  <span class="social" style="left:1055px;background:#5cc0ef" aria-label="Social network"></span>
  <span class="social" style="left:1093px;background:#1f7c9a" aria-label="Social network"></span>
  <span class="social" style="left:1130px;background:#d9262a" aria-label="Social network"></span>

</div>
</body>
</html>
```